Broschüren-Design für gemeinnützige Organisation
moonsparrows suchte ein neues Design in der Kategorie Broschüre und hat ein Projekt auf gestaltwerkstatt.de gestartet.
Zielgruppe
Als gemeinnützige Organisation unterstützen wir Kinder und Jugendliche, vor allem in den Bereichen Schul- und Berufsausbildung. Wir arbeiten vorwiegend in Ostafrika, vor allem in Tansania und Kenia. Mit dieser Broschüre wollen wir für unser neues Pilotprojekt werben, den Aufbau eines dualen Ausbildungszentrums für junge Menschen in Kenia. Ziel des Ausbildungszentrums ist es jungen Menschen eine qualifizierte Berufsausbildung zu ermöglichen und damit Perspektiven und Zukunft im Heimatland.
Unsere Zielgruppe: Menschen mit Herz und Weitblick von 18 bis 80+
Aufgabenstellung
Die Broschüre sollte handlich sein und leicht zum einstecken. Derzeit haben wir den Text und die Gestaltung auf das Format DIN lang hoch (105x210 mm, 12 Seiten) ausgelegt. Ist aber nur ein Vorschlag und kein muss.
Die einzige Vorgabe ist das orange aus dem Logo mit der Farbe #ff3300 Ansonsten gibt es keine Vorgaben was Schrift, Farbgestaltung, Layout, Form, Seitenanzahl...ect betrifft. Allerdings sollte darauf geachtet werden, dass die Textinhalte der Doppelseiten erhalten bleiben (z.B. Seite 2 links - Seite 3 rechts, usw.)
Mitgeliefert werden Fotos, die gerne Verwendung finden können. Sollten aber weitere oder aussagekräftigere Fotos und Hintergründe benötigt werden, sind wir absolut offen dafür.

```html
<!DOCTYPE html>
<html lang="de">
<head>
<meta charset="utf-8">
<title>moonsparrows – Broschüre Ausbildungszentrum</title>
<link href="https://fonts.googleapis.com/css2?family=Oswald:wght@500;600;700&family=Lato:wght@400;700;900&display=swap" rel="stylesheet">
<style>
  :root {
    --orange: #f04a14;
    --navy: #2e2c8e;
    --ink: #1d1d1f;
    --paper: #f3f3f3;
    --backdrop: #d8d7dc;
    --fold: #d2d2d4;
  }
  * { box-sizing: border-box; margin: 0; padding: 0; }
  html, body { width: 728px; height: 1200px; overflow: hidden; }
  body {
    background: var(--backdrop);
    font-family: "Lato", "Helvetica Neue", Arial, sans-serif;
    color: var(--ink);
    position: relative;
  }
  .spread {
    position: absolute;
    left: 34px;
    width: 660px;
    height: 560px;
    display: flex;
    box-shadow: 0 8px 24px rgba(0,0,0,.18);
  }
  .spread--one { top: 20px; }
  .spread--two { top: 620px; }
  .page {
    width: 330px;
    height: 100%;
    background: var(--paper);
    padding: 26px 24px 20px 26px;
    position: relative;
    overflow: hidden;
  }
  .page--left { border-right: 1px solid var(--fold); }
  .section-label {
    display: inline-block;
    background: var(--navy);
    color: #fff;
    font-family: "Oswald", "Arial Narrow", sans-serif;
    font-weight: 500;
    font-size: 8.5px;
    letter-spacing: .4px;
    text-transform: uppercase;
    padding: 3px 7px 2px;
    margin-bottom: 8px;
  }
  .headline {
    font-family: "Oswald", "Arial Narrow", sans-serif;
    font-weight: 600;
    color: var(--orange);
    font-size: 20px;
    line-height: 1.08;
    margin-bottom: 5px;
  }
  .headline--caps { text-transform: uppercase; font-size: 18px; }
  .body-text {
    font-size: 8.3px;
    line-height: 1.4;
    margin-bottom: 12px;
  }
  .sub-label {
    font-weight: 900;
    color: var(--navy);
    font-size: 8.5px;
    margin-top: 4px;
  }
  .course-list {
    list-style: none;
    font-size: 8.3px;
    font-weight: 700;
    line-height: 1.45;
    margin: 2px 0 6px 4px;
  }
  .course-list li::before { content: "• "; }
  .course-list .indent { padding-left: 8px; }
  .course-list .indent::before { content: ""; }
  .photo--mist {
    position: relative;
    margin: 0 -24px 14px -26px;
    height: 150px;
    background: linear-gradient(160deg, #9a9a9a 0%, #c9c9c9 35%, #6b6b6b 70%, #2e2e2e 100%);
  }
  .photo-caption {
    position: absolute;
    left: 40px;
    bottom: 14px;
    color: #fff;
    font-family: "Oswald", "Arial Narrow", sans-serif;
    font-weight: 500;
    font-style: italic;
    font-size: 8.5px;
    line-height: 1.25;
  }
  .photo-row {
    display: flex;
    align-items: flex-end;
    gap: 6px;
    margin-bottom: 10px;
  }
  .photo--kitchen {
    flex: 0 0 206px;
    height: 132px;
    margin-left: 10px;
    background: linear-gradient(135deg, #e8e6e3 0%, #b9b0a6 45%, #6a5548 75%, #c2703e 100%);
  }
  .side-caption {
    flex: 1;
    font-size: 6.4px;
    font-style: italic;
    line-height: 1.3;
  }
  .spacer { height: 18px; }
</style>
</head>
<body>

<section class="spread spread--one">
  <article class="page page--left">
    <span class="section-label">Die Ausgangslage</span>
    <h2 class="headline">Über 70% der Schulabgänger haben keinen Zugang zu einer Berufsausbildung</h2>
    <p class="body-text">Einen Beruf zu erlernen ist nur über den Besuch einer Universität, eines Colleges oder Polytechnikums möglich und das kostet sehr viel Geld. Geld, das die meisten Jugendlichen nicht haben. Nach Ende der Schulzeit, im Alter zwischen 16 und 18 Jahren, ist die Karriere der jungen Menschen bereits zu Ende. Sie werden Tagelöhner ohne Aussicht auf eine bessere Zukunft.</p>
    <h2 class="headline">Ein duales Ausbildungssystem gibt es nicht in Afrika</h2>
    <p class="body-text">Eine besondere Chance für Jugendliche in Deutschland ist unser duales Ausbildungssystem. Junge Menschen suchen sich nach Ende der Schulzeit eine bezahlte Lehrstelle und besuchen parallel dazu die Berufsschule. Dadurch erhalten sie eine gute Ausbildung und Deutschland bestens ausgebildete Fachkräfte. Diese Chance haben junge Menschen in Afrika nicht. Es gibt kein duales Ausbildungssystem in Afrika, auch nicht in Tansania oder Kenia. Die Jugendlichen bleiben auf der Strecke, ohne Aussicht auf eine bessere Zukunft.</p>
    <h2 class="headline">Jugendliche als billige Hilfskräfte ohne Chancen in ihrer Heimat</h2>
    <p class="body-text">Die Zahl der Jugendarbeitslosen ist hoch. Als Hilfsarbeiter und Tagelöhner werden sie ausgebeutet. Die Lebensbedingungen sind katastrophal und aussichtslos. Die jungen Menschen suchen verzweifelt nach einer Lösung, die es ohne Berufsausbildung in ihrer Heimat einfach nicht gibt.</p>
  </article>

  <article class="page page--right">
    <span class="section-label">Afrika im Wandel</span>
    <div class="photo--mist" role="img" aria-label="Schwarzweißfoto: junger Mensch mit Last auf dem Kopf auf einem nebligen Weg">
      <p class="photo-caption">Ohne Perspektiven verlassen junge Menschen<br>ihre Heimat, angezogen vom Leitstern Europa.</p>
    </div>
    <h2 class="headline">Globalisierung trifft die Ärmsten der Armen</h2>
    <p class="body-text">Durch die verschiedensten Handelsabkommen der Industrienationen mit den Ländern Afrikas sind viele der nationalen Märkte eingebrochen. Agrarprodukte aus aller Welt, Billigmöbel aus China oder Second-Hand-Ware aus Europa hat Menschen in traditionellen Berufen, mit denen früher noch ein gutes Einkommen zu erzielen war, die Existenzgrundlage entzogen.</p>
    <div class="spacer"></div>
    <h2 class="headline">Marktgerechte Fachausbildung schafft Zukunft für junge Menschen</h2>
    <p class="body-text">Berufe mit Zukunft, die auch vom Arbeitsmarkt gefragt sind, finden sich im Dienstleistungssektor, vor allem in den aufstrebenden Bereichen der gehobenen Gastronomie, sowie in der stetig wachsenden Hotel- und Tourismusbranche. Gut ausgebildete Fachkräfte in diesen Bereichen werden dringend gesucht.</p>
  </article>
</section>

<section class="spread spread--two">
  <article class="page page--left">
    <span class="section-label">Ausbildung vor Ort schafft Zukunft in der Heimat</span>
    <h2 class="headline">Perspektiven schaffen für junge Menschen durch qualifizierte Berufsausbildung</h2>
    <p class="body-text" style="margin-bottom:4px">Gut ausgebildete Fachkräfte werden dringend gesucht. Vor allem auch in den Bereichen der gehobenen Gastronomie und im Hotelfach. Im dualen Ausbildungssystem bieten wir jungen Menschen in ihrer Heimat folgende Ausbildungsberufe an</p>
    <ul class="course-list">
      <li>Koch (m/w/d)</li>
      <li>Konditor (m/w/d)</li>
      <li>Hotelkaufmann (m/w/d)</li>
      <li>Restaurantfachmann (m/w/d)</li>
      <li>Bürofachmann (m/w/d) mit Schwerpunkt</li>
      <li class="indent">Tourismus und Fremdsprachenkorrespondenz</li>
      <li>Haustechniker (m/w/d)</li>
    </ul>
    <p class="body-text">Mit Abschluss der Fachausbildung haben junge Menschen eine gesicherte Zukunft in ihrer Heimat.</p>
    <h2 class="headline">Ausbildungsqualität durch Ausbildungsrichtlinien der BKW und NABA</h2>
    <p class="body-text">Um eine gleichbleibende und fortlaufende Qualität in den Fachausbildungen zu gewährleisten wird nach den Richtlinien der BKW (Berufskammer Wirtschaft) ausgebildet. Zusätzlich werden nationale Richtlinien in der Ausbildung durch das zuständige Ministerium für Berufsbildung NABA integriert.</p>
  </article>

  <article class="page page--right">
    <div class="photo-row">
      <div class="photo--kitchen" role="img" aria-label="Foto: junger Koch in Kochjacke richtet in einer Profiküche einen Teller an"></div>
      <p class="side-caption">Ein gut ausgebildeter Koch (oder Köchin) ist auf dem Arbeitsmarkt sehr gefragt.</p>
    </div>
    <h2 class="headline headline--caps">Umsetzung durch<br>Integration einer dualen<br>Ausbildung vor Ort</h2>
    <p class="body-text" style="margin-bottom:6px">Um möglichst vielen jungen Menschen die Chance auf eine qualifizierte Fachausbildung zu ermöglichen ist der Aufbau eines dualen Ausbildungszentrums notwendig.</p>
    <h3 class="sub-label">Berufsschule</h3>
    <p class="body-text" style="margin-bottom:6px">In der Berufsschule wird der notwendige theoretische Teil der jeweiligen Fachausbildung unterrichtet. Im Unterschied zu Deutschland wird der Anteil der Berufsschule 40-50% der Ausbildungszeit in Anspruch nehmen, um bestehende Defizite aus der Schulausbildung der Jugendlichen auszugleichen.</p>
    <h3 class="sub-label">Lehrbetrieb</h3>
    <p class="body-text" style="margin-bottom:6px">Eine qualifizierte Ausbildung, die auf die Anforderungen des Arbeitsmarktes ausgerichtet ist, geht nur über die gleichzeitige praktische Ausbildung in einem Lehrbetrieb. Darum soll der praktische Teil der Ausbildung in einem der Berufsschule angeschlossenen Lehrhotel mit Gastronomiebereich stattfinden.</p>
    <h3 class="sub-label">Wohnheim</h3>
    <p class="body-text">Um auch jungen Menschen aus ländlichen Regionen die Chance auf Ausbildung zu ermöglichen soll ein Schülerwohnheim mit aufgebaut werden.</p>
  </article>
</section>

</body>
</html>
```